Larkspur Talent IT Recruiting firm needs a business card design for Recruiters, Sourcers, and Account

We need business cards that allow us to change all contact info, names, titles (Recruiter, Sourcer, Account Manager, Director, CEO, etc) per person since we have three offices, in three cities, Phoenix, Austin, and Las Vegas. We do recruiting and contractors for IT positions (Developers, Architects, Software Engineers, Security Engineers, Help Desk, DBAs, PMs, Scrum Masters, etc.) Our client companies are very diverse from Meridian 100 to silicone Valley type start-ups.

So, while we what hip, techie, and quirky, it still needs to be professional. Primary color we use is blue, with silver as a secondary color.

Target Market(s)

IT, Technology

Industry/Entity Type

Business

Contact Information for Business Card

Company name: Larkspur Talent, Inc.
Website: www.larkspurtalent.example
Logos for Careerloop, Blipster, and Myriada

Name, Title, Office Number, Cell Number, email

Font styles to use
Serif
Sans Serif

Colors
0455a3
d5d5d5

Requirements
Nice to have
• The grey I selected below is not necessary - but, would like silver included. I included a card design (File 3: LTI early trial example.jpg) that I had started on. It's very rough, and not quite what we're looking for, but what we did like is the logo, big, maybe a bit faded, off center, goes out of frame, etc. Still looking for other ideas - you are the pros! But, just an idea of a design element we liked.

```html
<!DOCTYPE html>
<html lang="en">
<head>
<meta charset="utf-8">
<title>Larkspur Talent – Business Card</title>
<link rel="stylesheet" href="https://fonts.googleapis.com/css2?family=Marcellus&family=Source+Sans+3:wght@400;600&display=swap">
<style>
  :root {
    --backdrop: #1c1c1c;
    --card-white: #ffffff;
    --card-grey: #545454;
    --brand-blue: #0455a3;
    --bright-blue: #1a7fd0;
    --ink: #2b2b2b;
    --muted: #555555;
    --silver: #d5d5d5;
    --stripe-grey: #5e5e5e;
  }
  * { margin: 0; padding: 0; box-sizing: border-box; }
  html, body {
    width: 1200px; height: 907px; overflow: hidden;
    background: var(--backdrop);
  }
  .canvas { position: relative; width: 1200px; height: 907px; }

  .card {
    position: absolute; left: 300px; width: 601px; height: 343px; overflow: hidden;
  }
  .card--front { top: 98px; background: var(--card-white); }
  .card--back { top: 475px; background: var(--card-grey); }

  .faint-emblem {
    position: absolute; left: -40px; top: -30px; width: 290px; height: 380px;
    border-radius: 50%;
    background: radial-gradient(ellipse at 45% 45%, rgba(0,0,0,0.045), rgba(0,0,0,0.02) 60%, rgba(0,0,0,0) 72%);
  }

  .brand { position: absolute; font-family: "Marcellus", serif; }
  .brand__row { display: flex; align-items: center; gap: 10px; }
  .brand__dot { width: 48px; height: 48px; border-radius: 50%; }
  .brand__name { font-size: 44px; line-height: 1; letter-spacing: 1px; }
  .brand__sub { font-size: 31px; line-height: 1; letter-spacing: 3px; text-align: right; margin-top: 2px; }
  .brand__tagline { font-size: 15px; letter-spacing: 1.6px; text-align: right; white-space: nowrap; }

  .card--front .brand { right: 40px; top: 36px; }
  .card--front .brand__dot { background: linear-gradient(180deg, var(--bright-blue), var(--brand-blue)); }
  .card--front .brand__name { color: var(--ink); }
  .card--front .brand__sub { color: var(--bright-blue); }
  .card--front .brand__tagline { color: var(--ink); margin-top: 24px; }

  .card--back .brand { left: 50%; top: 104px; transform: translateX(-50%); }
  .card--back .brand__dot { background: #ffffff; }
  .card--back .brand__name,
  .card--back .brand__sub,
  .card--back .brand__tagline { color: #ffffff; }
  .card--back .brand__tagline { margin-top: 14px; }

  .person { position: absolute; left: 33px; top: 198px; right: 41px; font-family: "Source Sans 3", sans-serif; }
  .person__name { font-size: 21px; color: var(--brand-blue); line-height: 1.2; }
  .person__title { display: flex; align-items: center; gap: 2px; font-size: 15px; color: var(--muted); margin-top: 4px; }
  .person__rule { flex: 1; height: 1px; background: #8a8a8a; }

  .contacts { position: absolute; top: 258px; font-family: "Source Sans 3", sans-serif; font-size: 15px; color: var(--ink); }
  .contacts li { list-style: none; display: flex; align-items: center; gap: 7px; height: 22px; }
  .contacts svg { width: 14px; height: 14px; fill: var(--brand-blue); }
  .contacts--phone { left: 33px; }
  .contacts--web { right: 41px; }

  .stripe { position: absolute; left: 0; bottom: 0; width: 601px; height: 10px; }

  .social { position: absolute; left: 0; right: 0; top: 291px; display: flex; justify-content: center; gap: 14px;
    font-family: "Source Sans 3", sans-serif; font-size: 13px; color: #ffffff; }
  .social span { display: flex; align-items: center; gap: 5px; }
  .social i { width: 12px; height: 12px; background: var(--bright-blue); border-radius: 2px; }
</style>
</head>
<body>
<div class="canvas">

  <section class="card card--front" aria-label="Card front">
    <div class="faint-emblem" role="img" aria-label="Large faded brand emblem running off the left edge"></div>

    <div class="brand">
      <div class="brand__row">
        <span class="brand__dot"></span>
        <span class="brand__name">LARKSPUR</span>
      </div>
      <div class="brand__sub">TALENT</div>
      <div class="brand__tagline">BUILDING TEAMS THAT FIT</div>
    </div>

    <div class="person">
      <div class="person__name">Dana Whitfield</div>
      <div class="person__title">Manager<span class="person__rule"></span></div>
    </div>

    <ul class="contacts contacts--phone">
      <li>
        <svg viewBox="0 0 16 16" aria-hidden="true"><path d="M4 1l2.5 3-1.6 1.8c.8 2 2.3 3.6 4.3 4.4L11 8.6l3 2.4-1.3 2.8C7.2 14 2 8.8 1.3 3.2z"/></svg>
        713-555-0142
      </li>
      <li>
        <svg viewBox="0 0 16 16" aria-hidden="true"><path d="M5 0h6a1.5 1.5 0 011.5 1.5v13A1.5 1.5 0 0111 16H5a1.5 1.5 0 01-1.5-1.5v-13A1.5 1.5 0 015 0zm0 2v8h6V2zm3 10a1 1 0 100 2 1 1 0 000-2z"/></svg>
        348-555-0187
      </li>
    </ul>

    <ul class="contacts contacts--web">
      <li>
        <svg viewBox="0 0 16 16" aria-hidden="true"><path d="M1 3h14v10H1zm1.5 1.2V5l5.5 3.6L13.5 5v-.8L8 7.7z"/></svg>
        info@larkspurtalent.example
      </li>
      <li>
        <svg viewBox="0 0 16 16" aria-hidden="true"><path d="M8 1a7 7 0 100 14A7 7 0 008 1zm0 1.3c.7.6 1.4 1.8 1.8 3.2H6.2C6.6 4.1 7.3 2.9 8 2.3zM5.9 7h4.2a10 10 0 010 2H5.9a10 10 0 010-2zm-1.5 0a12 12 0 000 2H2.5a5.7 5.7 0 010-2zm7.2 0h1.9a5.7 5.7 0 010 2h-1.9a12 12 0 000-2zM6.2 10.5h3.6c-.4 1.4-1.1 2.6-1.8 3.2-.7-.6-1.4-1.8-1.8-3.2z"/></svg>
        www.larkspurtalent.example
      </li>
    </ul>

    <svg class="stripe" viewBox="0 0 601 10" preserveAspectRatio="none" aria-hidden="true">
      <defs>
        <linearGradient id="stripe-blue" x1="0" x2="1">
          <stop offset="0" stop-color="#0a3f86"/>
          <stop offset="1" stop-color="#1a8ad8"/>
        </linearGradient>
      </defs>
      <polygon points="0,0 412,0 404,10 0,10" fill="url(#stripe-blue)"/>
      <polygon points="416,0 601,0 601,10 408,10" fill="var(--stripe-grey)"/>
    </svg>
  </section>

  <section class="card card--back" aria-label="Card back">
    <div class="brand">
      <div class="brand__row">
        <span class="brand__dot"></span>
        <span class="brand__name">LARKSPUR</span>
      </div>
      <div class="brand__sub">TALENT</div>
      <div class="brand__tagline">BUILDING TEAMS THAT FIT</div>
    </div>

    <div class="social">
      <span><i></i>Careerloop</span>
      <span><i></i>Blipster</span>
      <span><i></i>Myriada</span>
    </div>
  </section>

</div>
</body>
</html>
```